National Sales - Pick Up Truck Dealer

We need a logo design for a new vehicle dealership based in Sydney, Australia. The business name is Coastal Iron Haulers Motor Co. We will be selling American 'trucks/pick up trucks' like KRV, Torvan, Blaxer, Morrow T420, Kenzo Raptors, Morrow T640 and the likes.

These vehicles are a luxury option and we would like the logo to be strong, luxurious and masculine.Colours will be black and red or black and blue with the option of grey and white.

Target Market(s)

Men

Industry/Entity Type

Car Dealer

Contact Information for Business Card

Dennis Harlowe
Managing Director
0412 639 274
den@qelvtrk.com.au

Level 5, Brindle Parkway
17 Pemberly Lane
Baulkham Hills
NSW
Australia
Licence No: MD493152

Back of the card

qelvtrk.com.au

Font styles to use
Sans Serif

Colors

Designer to choose colors to be used in the design.

Requirements
Must have
• The company logo that is in the attachments, you can choose from the three which one you would like to work with. Must have vehicle images ....Please look at the attachments as they show examples of what we like and also provides potential images. If you choose to put an image on the front even if it is just the front of the vehicle can you please use the Black KRV Sorrento. Must have all details from the business card details section front and back
Nice to have
• N/A
Should not have
• No cars or standard trucks, please refer to the attached images to understand the product . Should not have any new logos or branding. No other colours besides what is in the logo you choose.

```html
<!DOCTYPE html>
<html lang="en">
<head>
<meta charset="utf-8">
<title>Coastal Iron Haulers Motor Co – Business Card</title>
<link rel="stylesheet" href="https://fonts.googleapis.com/css2?family=Cinzel:wght@600&family=Open+Sans:wght@400;600&display=swap">
<style>
  :root {
    --card-red: #b41f33;
    --card-navy: #35336f;
    --card-white: #f3f3f2;
    --text-light: #ffffff;
    --text-dark: #2e2e2e;
    --page-bg: #e6e6e4;
  }
  * { margin: 0; padding: 0; box-sizing: border-box; }
  html, body {
    width: 1200px; height: 900px; overflow: hidden;
    background: var(--page-bg);
  }
  .business-card {
    position: absolute; left: 150px; top: 174px;
    width: 900px; height: 552px;
    background: var(--card-red);
    box-shadow: 0 12px 30px rgba(0,0,0,0.18);
    overflow: hidden;
    font-family: "Open Sans", sans-serif;
  }
  .card-swoosh { position: absolute; inset: 0; }
  .holder-name {
    position: absolute; left: 55px; top: 62px;
    font-family: "Cinzel", serif; font-weight: 600;
    font-size: 30px; letter-spacing: 0.5px; line-height: 36px;
    color: var(--text-light);
  }
  .holder-title {
    position: absolute; left: 55px; top: 100px;
    font-size: 22px; color: var(--text-light);
  }
  .contact-list {
    position: absolute; left: 55px; top: 176px;
    list-style: none; color: var(--text-light);
    font-size: 23px; line-height: 33px;
  }
  .contact-list li { display: flex; align-items: center; gap: 8px; }
  .contact-icon { width: 19px; height: 19px; fill: var(--text-light); flex: none; }
  .brand-lockup {
    position: absolute; left: 480px; top: 318px;
    width: 390px;
    display: flex; align-items: center; gap: 14px;
  }
  .brand-dot {
    width: 46px; height: 46px; border-radius: 50%;
    background: var(--card-red); flex: none;
  }
  .brand-name {
    font-weight: 600; font-size: 30px; line-height: 36px;
    color: var(--card-navy);
  }
  .card-address {
    position: absolute; right: 42px; top: 452px;
    font-size: 20px; line-height: 29px; text-align: right;
    color: var(--text-dark);
  }
</style>
</head>
<body>
  <section class="business-card">
    <svg class="card-swoosh" viewBox="0 0 900 552" width="900" height="552" aria-hidden="true">
      <path d="M128 552 C240 310 550 140 900 84 L900 552 Z" fill="var(--card-navy)"/>
      <path d="M146 552 C264 328 568 156 900 96 L900 552 Z" fill="var(--card-white)"/>
    </svg>

    <h1 class="holder-name">DENNIS HARLOWE</h1>
    <p class="holder-title">Managing Director</p>

    <ul class="contact-list">
      <li>
        <svg class="contact-icon" viewBox="0 0 24 24"><path d="M3 9c0-3 4-5 9-5s9 2 9 5l-4 2-2-3H9L7 11 3 9zm4 3h10l3 8H4l3-8zm5 2a2.5 2.5 0 100 5 2.5 2.5 0 000-5z"/></svg>
        0412 639 274
      </li>
      <li>
        <svg class="contact-icon" viewBox="0 0 24 24"><path d="M7 1h10a2 2 0 012 2v18a2 2 0 01-2 2H7a2 2 0 01-2-2V3a2 2 0 012-2zm0 3v14h10V4H7zm5 15.5a1.2 1.2 0 100 2.4 1.2 1.2 0 000-2.4z"/></svg>
        0412 639 274
      </li>
      <li>
        <svg class="contact-icon" viewBox="0 0 24 24"><path d="M2 5h20v14H2V5zm2 2v.5l8 5.5 8-5.5V7H4zm0 3v7h16v-7l-8 5.5L4 10z"/></svg>
        den@qelvtrk.com.au
      </li>
      <li>
        <svg class="contact-icon" viewBox="0 0 24 24"><path d="M12 2a10 10 0 110 20 10 10 0 010-20zm-1 3.5C8 6 6 8 5 10l3 1 1 3-1 3 2 2 1-4 3-2-1-3-2-1V5.5zm4 .7V9l2 1 2 3v-1a7 7 0 00-4-5.8z"/></svg>
        qelvtrk.com.au
      </li>
    </ul>

    <div class="brand-lockup">
      <span class="brand-dot"></span>
      <span class="brand-name">Coastal Iron Haulers Motor Co</span>
    </div>

    <p class="card-address">
      Level 5, Brindle Parkway, 17 Pemberly Lane<br>
      Baulkham Hills NSW Australia · Licence No: MD493152
    </p>
  </section>
</body>
</html>
```